Business Cards for a law firm

Business cards for our law firm. Use our silhoette logo and OAK PARTNERS - check our website (www.oakpartners.example)

Contact Information for Business Card

our silhouette logo, OAK PARTNERS, 800-555-0147, Dorian Pemberton, dorian@oakpartners.example

Requirements
Must have
• our silhouette logo, OAK PARTNERS, 800-555-0147, Dorian Pemberton, dorian@oakpartners.example

```html
<!DOCTYPE html>
<html lang="en">
<head>
<meta charset="utf-8">
<title>Oak Partners – Business Cards</title>
<link rel="stylesheet" href="https://fonts.googleapis.com/css2?family=Montserrat:wght@400;500;700;800&display=swap">
<style>
  :root {
    --page: #d6d9dc;
    --navy: #2f3a6b;
    --navy-deep: #1f2a5a;
    --navy-light: #46527f;
    --suit: #262b45;
    --orange: #f5a21c;
    --white: #ffffff;
  }
  * { box-sizing: border-box; margin: 0; padding: 0; }
  html, body { width: 1179px; height: 1200px; overflow: hidden; }
  body {
    background: var(--page);
    font-family: "Montserrat", Arial, sans-serif;
    position: relative;
  }
  .card {
    position: absolute;
    left: 221px;
    width: 738px;
    height: 424px;
    overflow: hidden;
    color: var(--white);
  }
  .card--front { top: 161px; }
  .card--back { top: 619px; }
  .card__backdrop {
    position: absolute; inset: 0;
    background: linear-gradient(180deg, #34406f 0%, #2f3a6b 45%, #3a4574 70%, #2c3766 100%);
  }
  .brand {
    position: absolute; left: 0; right: 0;
    display: flex; align-items: center; justify-content: center; gap: 10px;
  }
  .brand__dot {
    width: 22px; height: 22px; border-radius: 50%;
    background: var(--white);
  }
  .brand__name {
    font-weight: 800; font-size: 28px; letter-spacing: 1.5px; color: var(--white);
  }
  .card--front .brand { top: 42px; }
  .card--back .brand { top: 80px; }
  .centered {
    position: absolute; left: 0; right: 0; text-align: center;
  }
  .tagline-firm {
    top: 113px; font-size: 21px; font-weight: 800; color: var(--orange);
  }
  .headline {
    top: 142px; font-size: 21px; font-weight: 700; line-height: 32.5px; text-transform: uppercase;
  }
  .results {
    top: 257px; font-size: 18px; font-weight: 400; line-height: 27px;
  }
  .cta {
    position: absolute; left: 234px; top: 330px; width: 267px; height: 34px;
    border-radius: 17px; background: var(--orange); color: var(--navy-deep);
    font-size: 14px; font-weight: 800; display: flex; align-items: center; justify-content: center;
    text-transform: uppercase;
  }
  .portrait {
    position: absolute; top: 140px; width: 228px; height: 259px;
    background: linear-gradient(180deg, rgba(38, 43, 69, 0) 0%, rgba(38, 43, 69, 0.55) 45%, var(--suit) 100%);
  }
  .portrait--left { left: 0; }
  .portrait--right { left: 510px; }
  .perk-band { position: absolute; left: 0; top: 377px; width: 738px; height: 47px; }
  .perk {
    position: absolute; display: flex; align-items: center; gap: 8px;
    color: var(--navy-deep); font-weight: 500;
  }
  .perk--consult { left: 26px; top: 399px; height: 25px; font-size: 16px; }
  .perk--fee { left: 240px; top: 382px; height: 36px; font-size: 19px; gap: 12px; }
  .perk--visit { left: 540px; top: 399px; height: 25px; font-size: 16px; }
  .contact-name {
    top: 171px; font-size: 28px; font-weight: 700; letter-spacing: 0.5px; text-transform: uppercase;
  }
  .contact-list {
    position: absolute; left: 0; right: 0; top: 220px;
    list-style: none; text-align: center;
  }
  .contact-list li {
    display: flex; flex-direction: column; align-items: center;
    font-size: 22px; font-weight: 400; line-height: 26px;
  }
  .contact-list li + li { margin-top: 7px; }
  .contact-list svg { display: block; margin-bottom: 4px; }
</style>
</head>
<body>

<section class="card card--front" aria-label="Business card front">
  <div class="card__backdrop" role="img" aria-label="Office building facade at dusk, tinted navy"></div>

  <div class="brand">
    <span class="brand__dot"></span>
    <span class="brand__name">OAK PARTNERS</span>
  </div>

  <p class="centered tagline-firm">THE OAK PARTNERS</p>
  <p class="centered headline">Injured?<br>Call the Oak<br>Partners!</p>
  <p class="centered results">Over $400,000,000<br>Recovered For Our Clients.</p>

  <div class="cta">Get a free consultation now</div>

  <div class="portrait portrait--left" role="img" aria-label="Photo of a partner in a dark suit"></div>
  <div class="portrait portrait--right" role="img" aria-label="Photo of a partner in a navy suit"></div>

  <svg class="perk-band" viewBox="0 0 738 47" aria-hidden="true">
    <rect x="0" y="22" width="230" height="25" fill="#ffffff"/>
    <rect x="510" y="22" width="228" height="25" fill="#ffffff"/>
    <polygon points="220,0 518,0 540,47 198,47" fill="#1f2a5a"/>
    <polygon points="231,0 506,0 527,47 212,47" fill="#ffffff"/>
  </svg>

  <div class="perk perk--consult">
    <svg width="18" height="20" viewBox="0 0 18 20" aria-hidden="true">
      <rect x="5" y="1" width="9" height="6" rx="1" fill="none" stroke="#f5a21c" stroke-width="1.2"/>
      <circle cx="4" cy="11" r="2" fill="none" stroke="#f5a21c" stroke-width="1.2"/>
      <circle cx="14" cy="11" r="2" fill="none" stroke="#f5a21c" stroke-width="1.2"/>
      <path d="M1 19c0-3 1.5-5 3-5s3 2 3 5M11 19c0-3 1.5-5 3-5s3 2 3 5" fill="none" stroke="#f5a21c" stroke-width="1.2"/>
    </svg>
    <span>Free Consultation</span>
  </div>

  <div class="perk perk--fee">
    <svg width="30" height="30" viewBox="0 0 30 30" aria-hidden="true">
      <circle cx="15" cy="15" r="14" fill="#2f3a6b" stroke="#c9cbd6" stroke-width="1.5"/>
      <circle cx="15" cy="15" r="7" fill="none" stroke="#f5a21c" stroke-width="1.2"/>
      <text x="15" y="19" text-anchor="middle" font-size="10" fill="#f5a21c" font-family="Montserrat, sans-serif">$</text>
    </svg>
    <span>No Fee Unless You Win</span>
  </div>

  <div class="perk perk--visit">
    <svg width="20" height="20" viewBox="0 0 20 20" aria-hidden="true">
      <circle cx="10" cy="10" r="9.5" fill="#2f3a6b"/>
      <path d="M10 4.5a3 3 0 0 0-3 3c0 2.3 3 6 3 6s3-3.7 3-6a3 3 0 0 0-3-3z" fill="none" stroke="#f5a21c" stroke-width="1.1"/>
      <circle cx="10" cy="7.5" r="1" fill="#f5a21c"/>
    </svg>
    <span>We’ll Come To You</span>
  </div>
</section>

<section class="card card--back" aria-label="Business card back">
  <div class="card__backdrop" role="img" aria-label="Office building facade at dusk, tinted navy"></div>

  <div class="brand">
    <span class="brand__dot"></span>
    <span class="brand__name">OAK PARTNERS</span>
  </div>

  <p class="centered contact-name">Dorian Pemberton</p>

  <ul class="contact-list">
    <li>
      <svg width="18" height="14" viewBox="0 0 18 14" aria-hidden="true">
        <path d="M1 5c0-2 3.5-3.5 8-3.5S17 3 17 5v1.2h-3.5V4.5h-9v1.7H1z" fill="#fff"/>
        <rect x="3.5" y="6.5" width="11" height="7" rx="1.2" fill="#fff"/>
        <circle cx="9" cy="10" r="2" fill="#2f3a6b"/>
      </svg>
      <span>800-555-0147</span>
    </li>
    <li>
      <svg width="18" height="13" viewBox="0 0 18 13" aria-hidden="true">
        <rect x="0.5" y="0.5" width="17" height="12" fill="#fff"/>
        <path d="M0.5 0.5 9 7.5 17.5 0.5" fill="none" stroke="#2f3a6b" stroke-width="1.2"/>
      </svg>
      <span>dorian@oakpartners.example</span>
    </li>
    <li>
      <svg width="17" height="17" viewBox="0 0 17 17" aria-hidden="true">
        <circle cx="8.5" cy="8.5" r="8" fill="#fff"/>
        <ellipse cx="8.5" cy="8.5" rx="3.5" ry="8" fill="none" stroke="#2f3a6b" stroke-width="1"/>
        <path d="M0.5 8.5h16" stroke="#2f3a6b" stroke-width="1"/>
      </svg>
      <span>www.oakpartners.example</span>
    </li>
  </ul>
</section>

</body>
</html>
```